Design my site www.brieflyledger.com

So here is what I am thinking in terms of design:

https://plenvo.com

https://www.skyluxair.com

http://kalvex.com/harbor-plaza-tower/

I want the theme to be white and blue (royal blue). I attached a paint picture of what I would like the site to look like in terms of placing the text. Generally, what I like about the sites above is that they are simple, you can navigate easily and have some kind of idea of what's going on by looking at the center (picture and motto). Let's establish a clear understanding of how the functional part of the site would look like. Please see the picture attached.

I want to keep it simple: On top would be the Name 'BRIEFLY ledger", somewhere to the right on top on the page would be 'Sign in" button.

In the center would be a picture (maybe a video) with the Motto (on top of it all in capital) OBSERVE NAVIGATE DECIDE and below would be the "sign up now"

Below the picture (like on kalvex.com site) or to the left on top of the page would be "About Us', "Press" "Contact Us' buttons.

Then once the user gets to his page his got 3 tabs " Press Headlines", "Events", " Briefings".

we would keep the same format I only have on the site, but separate for every Tab.

I do not want the user to get distracted. I also want him to be able to access the page though mobile phone and be able to get automatic updates just like Zorvan Pings without having to sign in daily.

The landing page must be minimalist yet with business/corporate feel where users can navigate easily and a "what you see is what you get" approach. You want an image or video (personally I prefer the video.. it does capture the users attention instantly, as long as it is an interesting video), with your taglines in it.

Sections available to public: About Us, Contact Us, Landing Page with Signup Option

Private: Public Sections + User Account Page, Tabs for (Events, Press Headlines, Briefings)

Target Market(s)

PR/media monitoring/diplomatic community

Coding

Coded - Design and coding required

Number of Pages Required

1 page

Font styles to use
Serif
Sans Serif

Colors
0255a3
ec1f27

Requirements
Must have
• a simple landing page, that is user friendly.
Nice to have
• a video with the explanation of how to navigate the site
Should not have
• too many colors, graphs etc.

```html
<!DOCTYPE html>
<html lang="en">
<head>
<meta charset="utf-8">
<title>BRIEFLY ledger — Press Headlines</title>
<link rel="stylesheet" href="https://fonts.googleapis.com/css2?family=Arimo:wght@400;700&family=Open+Sans:wght@400;600;700&display=swap">
<style>
  :root {
    --royal: #0255a3;
    --royal-dark: #034a8c;
    --signal-red: #ec1f27;
    --white: #ffffff;
    --label-grey: #7a7a7a;
    --text-dark: #3b3b3b;
    --field-top: #fbfbfb;
    --field-bottom: #e6e6e6;
    --field-border: #d9d9d9;
    --footer-top: #4a4a4a;
    --footer-bottom: #2f2f2f;
    --sky-light: #d3dfe2;
    --sky-mid: #9fb9c6;
    --city-deep: #6f8d9f;
  }
  * { box-sizing: border-box; margin: 0; padding: 0; }
  html, body { width: 1200px; height: 657px; overflow: hidden; }
  body { font-family: "Open Sans", Arial, sans-serif; color: var(--text-dark); }

  .page { position: relative; width: 1200px; height: 657px; overflow: hidden; }

  .hero-backdrop {
    position: absolute; inset: 0;
    background:
      linear-gradient(90deg, rgba(70,95,115,0.35) 0%, rgba(70,95,115,0.15) 38%, rgba(255,255,255,0) 46%),
      linear-gradient(180deg, var(--sky-mid) 0%, var(--sky-light) 30%, #c9d7dc 62%, var(--city-deep) 88%, #5d7a8c 100%);
  }

  .brand {
    position: absolute; left: 97px; top: 50px;
    font-family: "Arimo", Arial, sans-serif; font-weight: 700;
    font-size: 31px; letter-spacing: 0.2px; color: var(--white);
    text-transform: uppercase;
  }

  .sign-in {
    position: absolute; left: 1016px; top: 50px; width: 86px; height: 37px;
    border: none; border-radius: 3px;
    background: linear-gradient(180deg, #0a5fae 0%, var(--royal-dark) 100%);
    color: var(--white); font-family: "Arimo", Arial, sans-serif; font-size: 16px;
    box-shadow: 0 1px 2px rgba(0,0,0,0.25);
  }

  .dashboard {
    position: absolute; left: 150px; top: 147px; width: 899px; height: 377px;
    background: var(--white); box-shadow: 0 2px 6px rgba(0,0,0,0.25);
  }

  .tabs { display: flex; height: 49px; }
  .tab {
    flex: 1; display: flex; align-items: center; justify-content: center;
    background: var(--royal); color: var(--white);
    font-family: "Arimo", Arial, sans-serif; font-size: 21px; text-transform: uppercase;
    position: relative;
  }
  .tab.is-active { background: var(--signal-red); }
  .tab-divided::before {
    content: ""; position: absolute; left: 0; top: 10px; bottom: 10px;
    width: 1px; background: #033c73;
  }

  .field-label {
    position: absolute; left: 52px; font-size: 15.5px; line-height: 20px; color: var(--label-grey);
  }
  .text-field {
    position: absolute; left: 52px; width: 356px; height: 45px;
    border: 1px solid var(--field-border); border-radius: 2px;
    background: linear-gradient(180deg, var(--field-top) 0%, var(--field-bottom) 100%);
  }
  .select-caret { position: absolute; right: 14px; top: 19px; }

  .submit {
    position: absolute; left: 430px; top: 101px; width: 94px; height: 42px;
    border: none; border-radius: 2px;
    background: linear-gradient(180deg, #0a5fae 0%, var(--royal-dark) 100%);
    color: var(--white); font-family: "Open Sans", Arial, sans-serif;
    font-weight: 700; font-size: 14.5px; letter-spacing: 0.5px;
    box-shadow: 0 1px 2px rgba(0,0,0,0.25);
  }

  .sources {
    position: absolute; left: 573px; top: 100px; width: 221px; height: 234px;
    border: 1px solid #d4d4d4; background: var(--white);
  }
  .sources-header {
    height: 44px; background: var(--royal); color: var(--white);
    display: flex; align-items: center; padding-left: 17px; font-size: 16px;
  }
  .sources-header .checkbox { margin-right: 19px; border-color: #c9d6e4; background: #e9eef4; }
  .source-list { list-style: none; padding-top: 11px; }
  .source-list li {
    height: 25px; display: flex; align-items: center; padding-left: 17px;
    font-size: 14.5px; color: var(--text-dark);
  }
  .checkbox {
    width: 11px; height: 11px; border: 1px solid #9a9a9a;
    background: linear-gradient(180deg, #fdfdfd, #e3e3e3); margin-right: 17px; flex: none;
  }
  .scrollbar {
    position: absolute; right: 0; top: 44px; bottom: 0; width: 15px;
    background: #f4f4f4; border-left: 1px solid #e2e2e2;
  }
  .scroll-thumb {
    position: absolute; left: 1px; top: 60px; width: 12px; height: 24px;
    background: #f9f9f9; border: 1px solid #b8b8b8; border-radius: 2px;
  }

  .site-footer {
    position: absolute; left: 0; top: 607px; width: 1200px; height: 50px;
    background: linear-gradient(180deg, var(--footer-top) 0%, var(--footer-bottom) 100%);
    color: var(--white); font-size: 12.5px;
  }
  .copyright { position: absolute; left: 104px; top: 17px; }
  .footer-links { position: absolute; left: 969px; top: 17px; display: flex; gap: 19px; }
  .footer-links a { color: var(--white); text-decoration: none; }
</style>
</head>
<body>
<div class="page">
  <div class="hero-backdrop" role="img" aria-label="Photo of a city skyline seen through a glass office tower, in pale blue-grey haze"></div>

  <header>
    <div class="brand">BRIEFLY LEDGER</div>
    <button class="sign-in" type="button">SIGN IN</button>
  </header>

  <main class="dashboard">
    <nav class="tabs">
      <div class="tab is-active">Press Headlines</div>
      <div class="tab">Events</div>
      <div class="tab tab-divided">Briefings</div>
    </nav>

    <span class="field-label" style="top:70px">Keywords:</span>
    <div class="text-field" style="top:100px"></div>
    <button class="submit" type="button">SUBMIT</button>

    <span class="field-label" style="top:164px">Authors:</span>
    <div class="text-field" style="top:194px"></div>

    <span class="field-label" style="top:259px">Date range:</span>
    <div class="text-field" style="top:289px">
      <svg class="select-caret" width="11" height="6" viewBox="0 0 11 6"><path d="M0 0h11L5.5 6z" fill="#6a6a6a"/></svg>
    </div>

    <div class="sources">
      <div class="sources-header"><span class="checkbox"></span>All sources</div>
      <ul class="source-list">
        <li><span class="checkbox"></span>Pellham Gazette</li>
        <li><span class="checkbox"></span>Orvane Dispatch</li>
        <li><span class="checkbox"></span>Quillsend</li>
        <li><span class="checkbox"></span>Daybreak Wire</li>
        <li><span class="checkbox"></span>Vostra</li>
        <li><span class="checkbox"></span>Marrowby Post</li>
        <li><span class="checkbox"></span>Keldara</li>
      </ul>
      <div class="scrollbar">
        <svg style="position:absolute;left:3px;top:8px" width="9" height="5" viewBox="0 0 9 5"><path d="M4.5 0L9 5H0z" fill="#333"/></svg>
        <div class="scroll-thumb"></div>
        <svg style="position:absolute;left:3px;bottom:8px" width="9" height="5" viewBox="0 0 9 5"><path d="M0 0h9L4.5 5z" fill="#333"/></svg>
      </div>
    </div>
  </main>

  <footer class="site-footer">
    <span class="copyright">Copyright © 2016 BRIEFLY ledger</span>
    <div class="footer-links"><a href="#">Terms of Use</a><a href="#">Privacy</a></div>
  </footer>
</div>
</body>
</html>
```